Business Cards for IT Consulting Company (Managed Service Provider)

I am looking to have some business cards printed and would like some designs. We are an IT Consulting company based in Vancouver BC. I would like a nice clean and modern look to the cards. I have uploaded all the versions of my logo so parts can be used as needed. Here is a snippit from our website homepage:

Quillbrook Networks Ltd. is an IT Solutions Partner located in Vancouver BC, Canada. We offer IT solutions and support to customers in the greater Vancouver Area. With expertise in Microsoft platforms, as well as Linux and Mac OSX and over 12 years experience in the IT industry, Quillbrook Networks is dedicated to offering our clients top quality service and products. We take pride in the solutions we offer our customers. The greatest compliment a client can give us is to recommend our services.

Quillbrook Networks Ltd. offers a wide range of IT services from onsite service to remote support and managed service solutions. This allows clients to choose the support path that best suits their company’s needs. Supporting many different sized companies from small to enterprise level over the past 12 years Quillbrook Networks has the experience and expertise needed to ensure things run smoothly. Allowing our clients to focus on doing business.

Revolutionizing the way IT services are delivered.

Quillbrook Networks is dedicated to providing our clients with IT solutions that work and grow with them for years to come. This philosophy helps save money in the long run instead of replacing equipment constantly. Far too often IT solutions are not well thought out and while possibly solving the problem at hand, require replacement due to growth or quality within a very short time frame. Quillbrook Networks takes pride in providing solutions that will last and be able to accommodate growth without the need for replacement.

Industry/Entity Type

Information Technology

Contact Information for Business Card

Quillbrook Networks Ltd.
(Employee Name)
Eml: (Employees Email Address)
Web: quillbrook.me
Ph: 604-555-0148

Font styles to use
Serif
Sans Serif

Requirements
Must have
• The Company logo and company colors.
Nice to have
• - Our tag line: "Revolutionizing IT Services" or "Revolutionizing the way IT services are delivered."
• - Also I really like the idea of nature and technology together blending which is sort of where my logo came from so integrating that somehow onto the business cards would be great.

```html
<!DOCTYPE html>
<html lang="en">
<head>
<meta charset="utf-8">
<title>Quillbrook Networks – Business Card</title>
<link rel="stylesheet" href="https://fonts.googleapis.com/css2?family=Source+Sans+3:wght@400;600;700&display=swap">
<style>
  :root {
    --backdrop: #a4a5a7;
    --card-paper: #ececec;
    --brand-blue: #1a96d4;
    --brand-grey: #4d4f55;
    --text-grey: #55575c;
    --divider: #9c9ea2;
    --back-blue: #1c97d1;
    --white: #ffffff;
  }
  * { box-sizing: border-box; margin: 0; padding: 0; }
  html, body {
    width: 1105px;
    height: 1200px;
    overflow: hidden;
    background: var(--backdrop);
    font-family: "Source Sans 3", sans-serif;
  }
  .card {
    position: absolute;
    left: 182px;
    width: 747px;
    height: 427px;
    overflow: hidden;
  }
  .card--front { top: 119px; background: var(--card-paper); }
  .card--back { top: 636px; background: var(--back-blue); }

  /* Front */
  .brand-name {
    position: absolute;
    top: 112px;
    left: 0;
    width: 100%;
    text-align: center;
    color: var(--brand-blue);
    font-weight: 700;
    font-size: 50px;
    line-height: 1;
    letter-spacing: 0.5px;
  }
  .holder {
    position: absolute;
    top: 245px;
    right: 390px;
    text-align: right;
  }
  .holder__name {
    color: var(--brand-blue);
    font-weight: 600;
    font-size: 29px;
    line-height: 36px;
    margin-bottom: 4px;
  }
  .holder__address {
    color: var(--text-grey);
    font-size: 19px;
    line-height: 29px;
  }
  .divider {
    position: absolute;
    left: 378px;
    top: 247px;
    width: 1px;
    height: 100px;
    background: var(--divider);
  }
  .contact-list {
    position: absolute;
    left: 411px;
    top: 250px;
    list-style: none;
  }
  .contact-list__item {
    display: flex;
    align-items: center;
    height: 29px;
    color: var(--text-grey);
    font-size: 19px;
  }
  .contact-list__icon {
    width: 15px;
    height: 15px;
    margin-right: 9px;
    fill: var(--brand-blue);
  }
  .accent-band {
    position: absolute;
    bottom: 0;
    height: 20px;
  }
  .accent-band--blue { left: 0; width: 373px; background: var(--brand-blue); }
  .accent-band--grey { left: 375px; right: 0; background: var(--brand-grey); }

  /* Back */
  .hex-pattern {
    position: absolute;
    inset: 0;
    background: linear-gradient(135deg, #2aa1da 0%, #1a93cd 55%, #1b95cf 100%);
  }
  .back-brand {
    position: absolute;
    top: 190px;
    left: 0;
    width: 100%;
    text-align: center;
    color: var(--white);
    font-weight: 700;
    font-size: 40px;
    line-height: 1;
  }
  .tagline {
    position: absolute;
    top: 337px;
    left: 0;
    width: 100%;
    text-align: center;
    color: var(--white);
    font-weight: 600;
    font-size: 20px;
  }
</style>
</head>
<body>
  <section class="card card--front" aria-label="Business card front">
    <div class="brand-name">Quillbrook Networks Ltd.</div>

    <div class="holder">
      <p class="holder__name">Daniel Hart</p>
      <p class="holder__address">2931 Cedarview Lane</p>
      <p class="holder__address">Burnaby, BC V5G 1K2</p>
    </div>

    <div class="divider"></div>

    <ul class="contact-list">
      <li class="contact-list__item">
        <svg class="contact-list__icon" viewBox="0 0 24 24" aria-hidden="true"><path d="M6.6 10.8a15.1 15.1 0 0 0 6.6 6.6l2.2-2.2c.3-.3.7-.4 1-.2 1.1.4 2.3.6 3.6.6.6 0 1 .4 1 1V20c0 .6-.4 1-1 1C10.6 21 3 13.4 3 4c0-.6.4-1 1-1h3.5c.6 0 1 .4 1 1 0 1.3.2 2.5.6 3.6.1.3 0 .7-.2 1z"/></svg>
        604-555-0148
      </li>
      <li class="contact-list__item">
        <svg class="contact-list__icon" viewBox="0 0 24 24" aria-hidden="true"><path d="M2 5h20v14H2z" opacity=".9"/><path d="M2 5l10 8 10-8" fill="none" stroke="#ececec" stroke-width="2"/></svg>
        dhart@quillbrook.me
      </li>
      <li class="contact-list__item">
        <svg class="contact-list__icon" viewBox="0 0 24 24" aria-hidden="true"><circle cx="12" cy="12" r="10"/><path d="M2 12h20M12 2c3 3 3 17 0 20M12 2c-3 3-3 17 0 20" fill="none" stroke="#ececec" stroke-width="1.5"/></svg>
        www.quillbrook.me
      </li>
    </ul>

    <div class="accent-band accent-band--blue"></div>
    <div class="accent-band accent-band--grey"></div>
  </section>

  <section class="card card--back" aria-label="Business card back">
    <div class="hex-pattern" role="img" aria-label="Subtle tiled hexagon and cube line pattern in lighter blue"></div>
    <div class="back-brand">Quillbrook Networks</div>
    <p class="tagline">Revolutionizing IT Services</p>
  </section>
</body>
</html>
```